Bramblewood Joinery Website

My client Bramblewood Joinery is looking for a redesign for a Word Press Website. Their current site is at www.bramblewoodjoinery.example They are a custom cabinet company, but also create bathroom, living room, bar and entertainment and bedroom cabinets too. They would like a design that emulates the master craftsman work they do yet a contemporary style.

Their current site was designed using Flash elements.

Target Market(s)

Home owners and builders of high end homes

Industry/Entity Type

Entertainment

Font styles to use
Serif
Decorative

Requirements
Must have
• Must show their work and logo using a contemporary style.
Nice to have
• Sliders that showcase their projects.

```html
<!DOCTYPE html>
<html lang="en">
<head>
<meta charset="utf-8">
<title>Bramblewood Joinery</title>
<link rel="stylesheet" href="https://fonts.googleapis.com/css2?family=Open+Sans:ital,wght@0,400;0,600;1,400&family=Tinos&display=swap">
<style>
:root{
  --green:#34a63a;
  --green-dark:#1f3d22;
  --black:#000;
  --ink:#222;
  --muted:#777;
  --band:#f0eeee;
  --white:#fff;
  --hero-dark:#3b2a20;
  --hero-light:#c9bca6;
}
*{box-sizing:border-box;margin:0;padding:0}
html,body{width:725px;height:1200px;overflow:hidden;background:var(--white)}
body{position:relative;font-family:"Open Sans",sans-serif;color:var(--ink)}
.abs{position:absolute}
.navbar{left:0;top:49px;width:725px;height:33px;background:var(--black)}
.brand{left:60px;top:22px;width:56px;height:58px;border-radius:50%;background:var(--white);border:2px solid var(--black);display:flex;align-items:center;justify-content:center;text-align:center;font-size:7px;font-weight:600;line-height:1.2;color:var(--green);z-index:2}
.nav{left:155px;top:49px;height:33px;display:flex;font-family:"Tinos",serif;font-size:8px;color:var(--white);letter-spacing:.2px}
.nav span{display:flex;align-items:center;padding:0 11px;height:33px}
.nav .active{background:var(--green);padding:0 15px}
.search{left:572px;top:55px;width:93px;height:22px;background:var(--white);font-size:7px;padding:0 5px;display:flex;align-items:center;justify-content:space-between;color:#333}
.hero{left:0;top:82px;width:725px;height:337px;background:linear-gradient(90deg,var(--hero-dark) 0%,#5a4536 35%,#a39683 60%,var(--hero-light) 100%)}
.hero-card{left:208px;top:166px;width:292px;height:176px;background:rgba(40,40,40,.78);color:var(--white);font-size:25px;font-weight:600;line-height:37px;text-align:center;display:flex;align-items:center;justify-content:center}
.arrow{top:234px;width:20px;height:20px;border-radius:50%;background:#333}
h2{font-weight:400;font-size:16px;text-align:center;color:#111}
.welcome h2{position:absolute;top:434px;width:725px}
.welcome p{position:absolute;left:150px;top:460px;width:425px;font-size:7px;line-height:12.5px;text-align:center;color:var(--muted)}
.services-band{left:0;top:509px;width:725px;height:211px;background:var(--band)}
.services-band h2{margin-top:15px}
.service{top:555px;width:192px;height:142px;overflow:hidden}
.service .photo{height:98px}
.service .label{height:44px;background:var(--green);color:var(--white);text-align:center;padding-top:7px}
.service .label b{display:block;font-weight:400;font-size:12px;line-height:16px}
.service .label small{display:block;font-size:7px;line-height:12px;margin-top:1px}
.featured h2{position:absolute;top:731px;width:725px}
.product{top:758px;width:144px;text-align:center}
.product .photo{width:122px;height:122px;border-radius:50%;margin:0 auto;box-shadow:0 2px 5px rgba(0,0,0,.35)}
.product h3{font-weight:400;font-size:9px;color:var(--green);margin-top:8px}
.product p{font-size:7px;line-height:12.5px;color:#555;margin-top:2px}
.btn{display:inline-block;background:var(--black);color:var(--white);font-size:6.5px;padding:6px 10px;margin-top:7px}
.lower-band{left:0;top:993px;width:725px;height:152px;background:var(--band)}
.section-title{font-size:16px;font-weight:400;color:#111}
.quote{top:1038px;width:160px;font-size:7px;font-style:italic;line-height:12.5px;color:var(--muted)}
.quote cite{display:block;font-style:normal;color:var(--green);margin-top:7px}
.field{left:510px;width:129px;height:24px;background:var(--white);border:1px solid #ddd;font-size:7px;padding:0 8px;display:flex;align-items:center;color:#555}
.submit{left:539px;top:1107px;width:64px;height:18px;background:var(--green);color:var(--white);border-radius:3px;font-size:7px;display:flex;align-items:center;justify-content:center}
.footer{left:0;top:1145px;width:725px;height:55px;background:var(--black);color:var(--white);font-size:7px}
.social{width:20px;height:20px;border-radius:3px;background:#555}
</style>
</head>
<body>
<div class="abs navbar"></div>
<div class="abs brand">BRAMBLEWOOD<br>JOINERY</div>
<nav class="abs nav"><span class="active">HOME</span><span>ABOUT US</span><span>PRODUCT</span><span>BLOG</span><span>CABINETS &amp; FIXTURES</span><span>CONTACT US</span></nav>
<div class="abs search">search
<svg width="8" height="8" viewBox="0 0 10 10"><circle cx="4" cy="4" r="3" fill="none" stroke="#000" stroke-width="1.5"/><line x1="6.2" y1="6.2" x2="9" y2="9" stroke="#000" stroke-width="1.5"/></svg></div>

<div class="abs hero" role="img" aria-label="Wooden kitchen interior with granite island and pendant lights"></div>
<div class="abs hero-card">A NEW HOME<br>EXPERIENCE FOR<br>YOUR LIVING</div>
<svg class="abs arrow" style="left:25px" viewBox="0 0 20 20"><path d="M12 5 7 10l5 5" fill="none" stroke="#aaa" stroke-width="2"/></svg>
<svg class="abs arrow" style="left:680px" viewBox="0 0 20 20"><path d="M8 5l5 5-5 5" fill="none" stroke="#aaa" stroke-width="2"/></svg>

<section class="welcome"><h2>WELCOME TO OUR SITE</h2>
<p>Praesent justo dolor, lobortis quis, lobortis dignissim, pulvinar ac, loremwelcome to out siteFusce euismod consequat ante. Lorem ipsum dolor sit amet, consectetuer adipiscing elit. Pellentesque sed dolor. Aliquam congue fermentum nisl. Mauris accumsan nulla vel diam. Sed in lacus ut enim adipiscing aliquet. Nulla venenatis.</p></section>

<section class="abs services-band"><h2>OUR SERVICES</h2></section>
<div class="abs service" style="left:64px"><div class="photo" role="img" aria-label="Living room cabinetry" style="background:linear-gradient(#555,#2a2a2a)"></div><div class="label" style="background:var(--green-dark)"><b>LIVING ROOM</b><small>lobortis quis, lobortis dignissim, pulvinar ac</small></div></div>
<div class="abs service" style="left:267px"><div class="photo" role="img" aria-label="Modular kitchen with dark island" style="background:linear-gradient(#8a8580,#2b2622)"></div><div class="label"><b>MODULAR KITCHEN</b><small>lobortis quis, lobortis dignissim, pulvinar ac</small></div></div>
<div class="abs service" style="left:470px"><div class="photo" role="img" aria-label="Bathroom vessel basin" style="background:linear-gradient(#3a3a3a,#1e1e1e)"></div><div class="label"><b>BATH ROOM</b><small>lobortis quis, lobortis dignissim, pulvinar ac</small></div></div>
<svg class="abs" style="left:152px;top:613px" width="20" height="20" viewBox="0 0 20 20"><circle cx="8" cy="8" r="6" fill="none" stroke="#fff" stroke-width="2"/><path d="M5 8h6M8 5v6M12.5 12.5l5 5" stroke="#fff" stroke-width="2"/></svg>

<section class="featured"><h2>FEATURED PRODUCTS</h2></section>
<div class="abs product" style="left:60px"><div class="photo" role="img" aria-label="Bar cabinets with built-in oven" style="background:radial-gradient(#777,#2c2c2c)"></div><h3>BAR CABINETS</h3><p>Fusce euismod consequat ante. Lorem ipsum dolor sit amet, consectetuer adipi-scing elit. Pellentesque sed dolor.</p><span class="btn">READ MORE</span></div>
<div class="abs product" style="left:215px"><div class="photo" role="img" aria-label="Entertainment unit with fireplace" style="background:radial-gradient(#e8e4e0,#8a2a2a)"></div><h3>ENTERTAINMENT</h3><p>Fusce euismod consequat ante. Lorem ipsum dolor sit amet, consectetuer adipi-scing elit. Pellentesque sed dolor.</p><span class="btn">READ MORE</span></div>
<div class="abs product" style="left:371px"><div class="photo" role="img" aria-label="Bedroom furniture" style="background:radial-gradient(#d9a85a,#5a3320)"></div><h3>BED ROOM</h3><p>Fusce euismod consequat ante. Lorem ipsum dolor sit amet, consectetuer adipi-scing elit. Pellentesque sed dolor.</p><span class="btn">READ MORE</span></div>
<div class="abs product" style="left:525px"><div class="photo" role="img" aria-label="Kitchen with wooden floor" style="background:radial-gradient(#8a8a8a,#2a1e18)"></div><h3>KITCHEN</h3><p>Fusce euismod consequat ante. Lorem ipsum dolor sit amet, consectetuer adipi-scing elit. Pellentesque sed dolor.</p><span class="btn">READ MORE</span></div>

<section class="abs lower-band"></section>
<h2 class="abs section-title" style="left:86px;top:1008px">TESTIMONIALS</h2>
<blockquote class="abs quote" style="left:86px">“Lorem ipsum dolor sit amet, consectetur adipisic-ing elit, sed do eiusmod tempor incididunt ut labore et dolore magna aliqua. Ut enim ad minim veniam, quis nostrud exercitaullamco laboris nisi ut aliquip.”<cite>- ILSA MORELAND , CABINET DESIGNER</cite></blockquote>
<blockquote class="abs quote" style="left:277px">“Lorem ipsum dolor sit amet, consectetur adipisic-ing elit, sed do eiusmod tempor incididunt ut labore et dolore magna aliqua. Ut enim ad minim veniam, quis nostrud exercitaullamco laboris nisi ut aliquip.”<cite>- TEODOR VANCE , CHIEF QUALITY DEPT ;</cite></blockquote>
<h2 class="abs section-title" style="left:510px;top:1008px">CONTACT US</h2>
<div class="abs field" style="top:1034px">Name</div>
<div class="abs field" style="top:1069px">Email address</div>
<div class="abs submit">SUBMIT</div>

<footer class="abs footer">
<div class="abs" style="left:60px;top:11px">HOME &nbsp;I&nbsp; ABOUT US &nbsp;I&nbsp; PRODUCT &nbsp;I&nbsp; BLOG &nbsp;I&nbsp; CONTACT &amp; FIXTURES &nbsp;I&nbsp; CONTACT US</div>
<div class="abs" style="left:60px;top:29px">BRAMBLEWOOD JOINERY © 2015 PRIVACY POLICY</div>
<div class="abs social" style="left:541px;top:18px;background:var(--green)"></div>
<div class="abs social" style="left:567px;top:18px"></div>
<div class="abs social" style="left:593px;top:18px"></div>
<div class="abs social" style="left:619px;top:18px"></div>
<div class="abs social" style="left:645px;top:18px"></div>
</footer>
</body>
</html>
```